Business card design needed

Family General Practitioner/ Family Physician.
Logo is the logo of the Noble Guild of Family Healers Oceania
http://kpltw.varendo.example/ImageShelf/marks/pages/NGFHO%20mark_jpg.htm
Updates

Project Deadline Extended
Reason: Just a bit more time to make changes and the weekend for me to look at things closely and to choose. Thanks, Orin

Thanks for all the submissions. So many of them are really works of art. Not one of them are not good. The ones that I am eliminating are the ones that I think are not suitable for me personally only, and because if I don't, it makes it very difficult to decide as many of you are also sending me slight variations of a card. I have just decided to choose a second place card too. Can't thank you all enough. Good luck, Orin. P.S - Working today till 10 pm as the card says :-), so probably won't be able to give a feedback till late Saturday night or Sunday morning here in Sydney, Australia. 

Project Deadline Extended
Reason: Just added a second place to the budget and realised that Australia is ahead of the rest of the world in the time zone (only :-) - don't want to offend anyone or start a debate!! ) , so Monday deadline will mean it will be a weekend for the rest of the world. Just wanted to give everyone more time to submit their best, especially since I will be picking a second card too. Can't thank everyone enough for the submissions. P.S - Not keen on photos on the card.

Industry/Entity Type

Business

Contact Information for Business Card

Dr. Orin Halvey M.B.B.S., F.N.G.F.H.O
Family General Practitioner
Address, timings, phone and fax number on the back.

Requirements
Must have
• Timings
Mon 7 am - 7 pm
Tues 7 am - 12 pm
Wed 7 am - 10 pm
Thurs 7 am - 12 pm
Fri 7 am - 8 pm
Sat 8 am - 10 pm
Sun - Off

```html
<!DOCTYPE html>
<html lang="en">
<head>
<meta charset="utf-8">
<title>Dr Orin Halvey – Business Card</title>
<link rel="stylesheet" href="https://fonts.googleapis.com/css2?family=Jost:ital,wght@0,400;0,500;0,600;0,700;1,600&family=Marcellus&family=Marcellus+SC&family=PT+Sans+Narrow:wght@700&display=swap">
<style>
  :root {
    --stage: #e7e5e2;
    --label: #2a2a2a;
    --card: #ffffff;
    --navy: #2e3192;
    --aqua: #a8dde3;
    --ink: #3a3a3a;
    --rule: #6b6b6b;
    --sky-top: #dbe7f4;
    --sky-bottom: #b8d0ea;
    --white: #ffffff;
  }
  * { margin: 0; padding: 0; box-sizing: border-box; }
  html, body { width: 1200px; height: 788px; overflow: hidden; }
  body { background: var(--stage); position: relative; font-family: "Jost", sans-serif; color: var(--ink); }

  .variant-label { position: absolute; font-family: "Jost", sans-serif; font-size: 21px; color: var(--label); transform: translateX(-50%); }

  .card { position: absolute; width: 525px; height: 300px; border-radius: 18px; background: var(--card); overflow: hidden; box-shadow: 0 4px 10px rgba(0,0,0,.25); }
  .card--front { left: 338px; top: 72px; }
  .card--back-photo { left: 53px; top: 445px; }
  .card--back-tint { left: 621px; top: 445px; background: linear-gradient(100deg, var(--sky-top), var(--sky-bottom)); }

  /* front */
  .swoosh { position: absolute; inset: 0; }
  .doctor-name { position: absolute; left: 38px; top: 28px; font-size: 28px; font-weight: 600; color: var(--navy); letter-spacing: .3px; }
  .credentials { position: absolute; left: 38px; top: 64px; font-family: "Marcellus", serif; font-size: 20px; color: var(--navy); letter-spacing: 1.5px; }
  .role { position: absolute; left: 38px; top: 106px; font-family: "Marcellus SC", serif; font-size: 15px; color: var(--navy); letter-spacing: .8px; }
  .guild { position: absolute; right: 52px; top: 34px; width: 96px; display: flex; flex-direction: column; align-items: center; gap: 5px; text-align: center; font-family: "Marcellus", serif; font-size: 10px; line-height: 1.2; color: var(--navy); }
  .guild-dot { width: 30px; height: 30px; border-radius: 50%; background: var(--navy); }
  .contact { position: absolute; left: 36px; top: 206px; list-style: none; font-size: 14px; color: var(--ink); line-height: 18px; }
  .contact li { display: flex; align-items: center; gap: 6px; }
  .contact svg { width: 10px; height: 10px; fill: var(--navy); }
  .address { position: absolute; right: 15px; bottom: 11px; text-align: right; font-size: 12.5px; line-height: 16px; color: var(--white); font-style: normal; }

  /* backs */
  .photo-wash { position: absolute; inset: 0; background: radial-gradient(ellipse at 30% 40%, rgba(214,170,150,.35), rgba(200,215,235,.25) 45%, rgba(255,255,255,0) 75%); }
  .back-title { position: absolute; top: 14px; left: 0; right: 0; text-align: center; font-family: "Marcellus SC", serif; font-size: 22px; letter-spacing: 1px; color: var(--ink); }
  .rule-h { position: absolute; left: 0; right: 0; height: 1px; background: var(--rule); }
  .rule-h--top { top: 52px; }
  .rule-h--bottom { top: 263px; }
  .rule-v { position: absolute; left: 265px; top: 52px; width: 1px; height: 211px; background: var(--rule); }
  .timings { position: absolute; left: 44px; top: 62px; width: 190px; }
  .timings-title { font-size: 17px; font-weight: 600; font-style: italic; text-align: center; width: 172px; margin-bottom: 2px; }
  .timings-list { display: grid; grid-template-columns: 61px auto; font-size: 17px; line-height: 23.3px; }
  .timings-list dt { font-weight: 600; }
  .appointment { position: absolute; left: 277px; top: 64px; right: 14px; font-size: 17px; }
  .appointment-title { font-size: 19px; font-weight: 400; margin-bottom: 16px; }
  .field { display: flex; align-items: flex-end; height: 39px; }
  .field .blank { flex: 1; border-bottom: 1px solid var(--ink); height: 18px; margin-left: 4px; }
  .field--spare .blank { margin-left: 9px; }
  .field--time .blank { flex: none; width: 126px; margin-left: 0; margin-right: 4px; }
  .notice { position: absolute; top: 274px; left: 0; right: 0; text-align: center; font-family: "PT Sans Narrow", sans-serif; font-weight: 700; font-size: 12.5px; color: var(--ink); }
</style>
</head>
<body>

<span class="variant-label" style="left:600px; top:32px;">Front</span>
<span class="variant-label" style="left:316px; top:404px;">Back - 2</span>
<span class="variant-label" style="left:896px; top:404px;">Back - 3</span>

<section class="card card--front">
  <svg class="swoosh" viewBox="0 0 525 300" preserveAspectRatio="none" aria-hidden="true">
    <path d="M0 270 C180 262 380 212 525 112 L525 160 C380 240 180 275 0 278 Z" fill="var(--aqua)"/>
    <path d="M0 266 C190 272 390 230 525 155 L525 300 L0 300 Z" fill="var(--navy)"/>
    <path d="M0 272 C190 276 390 236 525 161" fill="none" stroke="var(--white)" stroke-width="3"/>
  </svg>
  <h1 class="doctor-name">Dr Orin Halvey</h1>
  <p class="credentials">M.B.B.S., F.N.G.F.H.O</p>
  <p class="role">Family General Practitioner</p>
  <div class="guild"><span class="guild-dot"></span><span>Noble Guild of Family Healers Oceania</span></div>
  <ul class="contact">
    <li><svg viewBox="0 0 10 10"><rect x="2.5" y="0" width="5" height="10" rx="1"/></svg>02 9417 6380</li>
    <li><svg viewBox="0 0 10 10"><rect x="2" y="0" width="6" height="4"/><rect x="0" y="4" width="10" height="6" rx="1"/></svg>02 9417 6391</li>
  </ul>
  <address class="address">Upper Level, Olive Court<br>Harbour Gate Shopping Centre<br>Elm Ridge, NSW 2190</address>
</section>

<section class="card card--back-photo">
  <div class="photo-wash" role="img" aria-label="Faint photo of children playing together, washed out behind the text"></div>
  <h2 class="back-title">Caring about your health</h2>
  <div class="rule-h rule-h--top"></div>
  <div class="rule-v"></div>
  <div class="rule-h rule-h--bottom"></div>
  <div class="timings">
    <p class="timings-title">Clinic Timings</p>
    <dl class="timings-list">
      <dt>Mon</dt><dd>7 am &nbsp;-&nbsp; 7 pm</dd>
      <dt>Tues</dt><dd>7 am &nbsp;-&nbsp; 12 pm</dd>
      <dt>Wed</dt><dd>7 am &nbsp;-&nbsp; 10 pm</dd>
      <dt>Thurs</dt><dd>7 am &nbsp;-&nbsp; 12 pm</dd>
      <dt>Fri</dt><dd>7 am &nbsp;-&nbsp; 8 pm</dd>
      <dt>Sat</dt><dd>8 am &nbsp;-&nbsp; 10 pm</dd>
      <dt>Sun</dt><dd>Off</dd>
    </dl>
  </div>
  <div class="appointment">
    <p class="appointment-title">Your Appointment</p>
    <div class="field">Name<span class="blank"></span></div>
    <div class="field field--spare"><span class="blank"></span></div>
    <div class="field">Date<span class="blank"></span></div>
    <div class="field field--time">time<span class="blank"></span>am / pm</div>
  </div>
  <p class="notice">24 business hours notice required for cancellations</p>
</section>

<section class="card card--back-tint">
  <h2 class="back-title">Caring about your health</h2>
  <div class="rule-h rule-h--top"></div>
  <div class="rule-v"></div>
  <div class="rule-h rule-h--bottom"></div>
  <div class="timings">
    <p class="timings-title">Clinic Timings</p>
    <dl class="timings-list">
      <dt>Mon</dt><dd>7 am &nbsp;-&nbsp; 7 pm</dd>
      <dt>Tues</dt><dd>7 am &nbsp;-&nbsp; 12 pm</dd>
      <dt>Wed</dt><dd>7 am &nbsp;-&nbsp; 10 pm</dd>
      <dt>Thurs</dt><dd>7 am &nbsp;-&nbsp; 12 pm</dd>
      <dt>Fri</dt><dd>7 am &nbsp;-&nbsp; 8 pm</dd>
      <dt>Sat</dt><dd>8 am &nbsp;-&nbsp; 10 pm</dd>
      <dt>Sun</dt><dd>Off</dd>
    </dl>
  </div>
  <div class="appointment">
    <p class="appointment-title">Your Appointment</p>
    <div class="field">Name<span class="blank"></span></div>
    <div class="field field--spare"><span class="blank"></span></div>
    <div class="field">Date<span class="blank"></span></div>
    <div class="field field--time">time<span class="blank"></span>am / pm</div>
  </div>
  <p class="notice">24 business hours notice required for cancellations</p>
</section>

</body>
</html>
```